Velmarotix - world unique technology for better life - please let them know who am i at first sight

We need a new business card for company which is a provider of unique crystal based technology suitable for all living being. For more information and final design you can use our brochure (our colours are black and blue from brochure).
We use Verdana font

Industry/Entity Type

Business

Contact Information for Business Card

regular dimension

Font styles to use
Other font styles liked:
• Verdana

Requirements
Must have
• Logo
• name
• function/position
• phone
• mobile
• e-mail
• adress
Nice to have
• inovative design (technology directed)

```html
<!DOCTYPE html>
<html lang="en">
<head>
<meta charset="utf-8">
<title>Velmarotix business card</title>
<link rel="stylesheet" href="https://fonts.googleapis.com/css2?family=Open+Sans:wght@300;400;600&display=swap">
<style>
  :root {
    --blue-deep: #1a9fd3;
    --blue-mid: #22b6e3;
    --blue-light: #4fcdef;
    --white: #ffffff;
    --paper: #f1f2f3;
    --ink: #1d1f21;
    --ink-soft: #4a4d50;
    --backdrop: #e4e6e8;
  }
  * { box-sizing: border-box; margin: 0; padding: 0; }
  html, body {
    width: 1200px; height: 858px; overflow: hidden;
    background: var(--backdrop);
    font-family: "Open Sans", Verdana, sans-serif;
  }
  .sheet {
    width: 1200px; height: 858px;
    display: flex; align-items: center; justify-content: center; gap: 60px;
  }
  .card {
    width: 525px; height: 300px; position: relative; overflow: hidden;
    border-radius: 3px;
    box-shadow: 0 6px 18px rgba(0,0,0,.18);
  }

  /* Front */
  .card-front { background: linear-gradient(135deg, var(--blue-deep) 0%, var(--blue-light) 55%, var(--blue-mid) 100%); }
  .front-brand {
    position: absolute; left: 44px; top: 62px;
    display: flex; align-items: center; gap: 20px;
  }
  .brand-dot {
    width: 84px; height: 84px; border-radius: 50%;
    border: 3px solid var(--white);
  }
  .brand-name {
    color: var(--white); font-weight: 300; font-size: 46px; letter-spacing: 1px;
    text-transform: uppercase; line-height: 1;
  }
  .front-band {
    position: absolute; left: 0; right: 0; top: 178px; height: 58px;
    background: linear-gradient(180deg, #ffffff, #e9ebec);
  }
  .front-social {
    position: absolute; left: 0; right: 0; top: 236px; bottom: 0;
    background: var(--blue-deep);
    display: flex; align-items: center; justify-content: space-around; padding: 0 40px;
  }
  .social-dot { width: 14px; height: 14px; border-radius: 50%; background: var(--white); opacity: .9; }

  /* Back */
  .card-back { background: var(--paper); }
  .back-top {
    position: absolute; left: 0; right: 0; top: 0; height: 118px;
    background: linear-gradient(135deg, var(--blue-deep), var(--blue-light));
  }
  .back-brand {
    position: absolute; right: 34px; top: 40px;
    display: flex; align-items: center; gap: 10px;
  }
  .back-brand .brand-dot { width: 32px; height: 32px; border-width: 2px; }
  .back-brand .brand-name { font-size: 24px; }
  .person {
    position: absolute; right: 34px; top: 138px; text-align: right; color: var(--ink);
  }
  .person-name { font-size: 22px; font-weight: 400; }
  .person-role { font-size: 13px; color: var(--ink-soft); margin-top: 2px; }
  .contacts {
    position: absolute; left: 34px; bottom: 26px;
    list-style: none; color: var(--ink); font-size: 12.5px; line-height: 1.55;
  }
  .contacts li { display: flex; align-items: center; gap: 8px; }
  .contacts svg { width: 15px; height: 15px; flex: none; }
  .contacts .addr-line { padding-left: 23px; }
</style>
</head>
<body>
<main class="sheet">
  <section class="card card-front" aria-label="Card front">
    <div class="front-brand">
      <span class="brand-dot"></span>
      <span class="brand-name">Velmarotix</span>
    </div>
    <div class="front-band"></div>
    <div class="front-social" aria-label="Social channels">
      <span class="social-dot"></span><span class="social-dot"></span><span class="social-dot"></span>
      <span class="social-dot"></span><span class="social-dot"></span><span class="social-dot"></span>
    </div>
  </section>

  <section class="card card-back" aria-label="Card back">
    <div class="back-top"></div>
    <div class="back-brand">
      <span class="brand-dot"></span>
      <span class="brand-name">Velmarotix</span>
    </div>
    <div class="person">
      <p class="person-name">Your Name</p>
      <p class="person-role">Position</p>
    </div>
    <ul class="contacts">
      <li>
        <svg viewBox="0 0 16 16"><rect width="16" height="16" rx="3" fill="#1d1f21"/><rect x="5" y="3" width="6" height="10" rx="1" fill="none" stroke="#22b6e3" stroke-width="1.4"/></svg>
        000-0000-0000
      </li>
      <li>
        <svg viewBox="0 0 16 16"><rect width="16" height="16" rx="3" fill="#1d1f21"/><path d="M4 4c0 5 3 8 8 8l1-2-2-1-1 1c-2-1-3-2-4-4l1-1-1-2z" fill="#22b6e3"/></svg>
        +385(0) 51 420 377
      </li>
      <li>
        <svg viewBox="0 0 16 16"><rect width="16" height="16" rx="3" fill="#1d1f21"/><rect x="3" y="4.5" width="10" height="7" fill="none" stroke="#22b6e3" stroke-width="1.3"/><path d="M3 4.5l5 4 5-4" fill="none" stroke="#22b6e3" stroke-width="1.3"/></svg>
        info@velmarotix.eu
      </li>
      <li>
        <svg viewBox="0 0 16 16"><rect width="16" height="16" rx="3" fill="#1d1f21"/><circle cx="8" cy="8" r="4.5" fill="none" stroke="#22b6e3" stroke-width="1.3"/><path d="M3.5 8h9M8 3.5v9" stroke="#22b6e3" stroke-width="1"/></svg>
        www.velmarotix.eu
      </li>
      <li>
        <svg viewBox="0 0 16 16"><rect width="16" height="16" rx="3" fill="#1d1f21"/><path d="M8 13s-4-4-4-7a4 4 0 0 1 8 0c0 3-4 7-4 7z" fill="#22b6e3"/><circle cx="8" cy="6" r="1.4" fill="#1d1f21"/></svg>
        28-34 Harrow Lane London
      </li>
      <li class="addr-line">E2 7QN United Kingdom</li>
    </ul>
  </section>
</main>
</body>
</html>
```